the theater production needs a poster design

we
we need a poster design for the Opera 'Pip and Marigold'
the show will be put on the stage on May 18.
the week is family week.
we launch the Opera on the stage size of 700 people
the opera will be performed by Orchestra of 30 musicians and 7 singers
most of audience are parents with children.
we will use the final design for the printing and mobile marketing.

here is the informations

Opera 'Pip and Marigold'

date: 2024.5.18 Saturday 2pm, 5pm
Dorim Stagehall
Ticket $50
BOOK _02-531-6092
Music Director_Soyeon Park, Producer Minho Park

```html
<!DOCTYPE html>
<html lang="en">
<head>
<meta charset="utf-8">
<title>Opera Pip &amp; Marigold — Poster</title>
<link href="https://fonts.googleapis.com/css2?family=Cinzel:wght@400;600;700&family=Oswald:wght@400;500;600&display=swap" rel="stylesheet">
<style>
  :root {
    --page-bg: #e4e5e7;
    --poster-black: #070708;
    --title-red: #d5202a;
    --text-white: #f4f1ec;
    --night-blue: #1d3350;
    --dusk-blue: #35567a;
    --lamp-amber: #c98a3e;
    --roof-brown: #4a3326;
    --stage-warm: #3a2418;
  }
  * { margin: 0; padding: 0; box-sizing: border-box; }
  html, body {
    width: 865px; height: 1200px; overflow: hidden;
    background: var(--page-bg);
  }
  .poster {
    position: absolute; left: 64px; top: 64px;
    width: 737px; height: 1072px;
    background: var(--poster-black);
    overflow: hidden;
    color: var(--text-white);
    text-align: center;
  }
  .hero-art {
    position: absolute; left: 0; top: 0; width: 100%; height: 640px;
    background:
      radial-gradient(ellipse at 20% 50%, rgba(201,138,62,.45) 0%, rgba(201,138,62,0) 30%),
      radial-gradient(ellipse at 88% 28%, rgba(201,138,62,.35) 0%, rgba(201,138,62,0) 22%),
      radial-gradient(ellipse at 55% 35%, rgba(120,82,60,.55) 0%, rgba(120,82,60,0) 40%),
      linear-gradient(180deg, var(--night-blue) 0%, var(--dusk-blue) 22%, var(--roof-brown) 48%, var(--poster-black) 82%);
  }
  .audience-art {
    position: absolute; left: 0; bottom: 0; width: 100%; height: 190px;
    background:
      radial-gradient(ellipse at 50% 100%, rgba(201,138,62,.35) 0%, rgba(201,138,62,0) 60%),
      linear-gradient(180deg, var(--poster-black) 0%, var(--stage-warm) 70%, #55341f 100%);
  }
  .content { position: absolute; left: 0; top: 0; width: 100%; }
  .genre {
    position: absolute; top: 345px; width: 100%;
    font-family: "Cinzel", serif; font-weight: 600;
    font-size: 36px; letter-spacing: 14px; padding-left: 14px;
  }
  .title-main {
    position: absolute; top: 382px; width: 100%;
    font-family: "Cinzel", serif; font-weight: 700;
    font-size: 90px; line-height: 1; color: var(--title-red);
  }
  .title-sub {
    position: absolute; top: 470px; width: 100%;
    font-family: "Cinzel", serif; font-weight: 700;
    font-size: 72px; line-height: 1;
  }
  .weekday {
    position: absolute; top: 545px; width: 100%;
    font-family: "Cinzel", serif; font-weight: 600; font-size: 28px;
  }
  .date {
    position: absolute; top: 575px; width: 100%;
    font-family: "Cinzel", serif; font-weight: 600; font-size: 42px;
    color: var(--title-red); line-height: 1;
  }
  .showtimes {
    position: absolute; top: 622px; width: 100%;
    font-family: "Cinzel", serif; font-size: 15px; letter-spacing: .5px;
  }
  .ticket {
    position: absolute; top: 673px; left: 219px;
    width: 300px; height: 58px;
    border: 3px solid var(--title-red); border-radius: 29px;
    font-family: "Oswald", sans-serif; font-weight: 600;
    font-size: 40px; line-height: 50px; letter-spacing: 2px;
  }
  .booking {
    position: absolute; top: 738px; width: 100%;
    font-family: "Oswald", sans-serif; font-size: 30px; letter-spacing: 2px;
  }
  .credits {
    position: absolute; top: 796px; width: 100%;
    font-family: "Oswald", sans-serif; font-weight: 500;
    font-size: 26px; line-height: 33px; letter-spacing: 1px;
  }
</style>
</head>
<body>
  <main class="poster">
    <div class="hero-art" role="img" aria-label="Illustration of two children looking up beside lamp-lit storybook cottages at night"></div>
    <div class="audience-art" role="img" aria-label="Illustration of an orchestra and audience in a theatre"></div>
    <div class="content">
      <p class="genre">OPERA</p>
      <h1 class="title-main">PIP</h1>
      <p class="title-sub">&amp; MARIGOLD</p>
      <p class="weekday">Saturday</p>
      <p class="date">18 MAY 2024</p>
      <p class="showtimes">AT 2PM, 5PM DORIM STAGEHALL</p>
      <p class="ticket">TICKET $50</p>
      <p class="booking">BOOK 02-531-6092</p>
      <p class="credits">MUSIC DIRECTOR SOYEON PARK<br>PRODUCER MINHO PARK</p>
    </div>
  </main>
</body>
</html>
```